Tonic und Gin Tonic
Zielgruppe
Von Altenburg in alle Welt
Heute arbeiten über 65 Mitarbeiter aus der Region. Auf 30.000 Quadratmetern werden täglich 200.000 Flaschen Hochprozentiges produziert und abgefüllt. Weitere Produktionsflächen auf 85.000 Quadratmetern in Polen dienen ebenfalls der Unternehmensaktivität Mit einer Produktion von mehr als 30 Millionen Flaschen im Jahr ist die Kesselbacher Brennerei heute einer der größten Spirituosenhersteller Deutschlands. Und in der Tat könnte man sich hier verlaufen. Die Lagerkapazität reicht für zwei Millionen Flaschen. Die Getränkeauswahl ist immens. Die Produktion erfolgt auf acht automatisierten Abfülllinien. Die Kesselbacher Spezialitäten werden ins In- und Ausland verschickt. Nach Israel, nach China und Amerika – die Liste ist lang. „Wir haben mehr als 120 verschiedene Produkte im Programm, Frucht- und Sahneliköre, Klare und Kräuterschnäpse“.
Neben Glas und PET fertigen wir Dosen in 200 ml, 250 ml slim, 330 ml und 500 ml.
Aufgabenstellung
Kreativ, einzigartig, ansprechend, marktkonform und realistisch, keine Kunst! Da wir bereits mit nationalen und internationalen Firmen zusammenarbeiten, auch Polen, Bulgarien und Rumänien kennen wir die Preislage bezüglich Design und Entwicklung und suchen einen Partner / Designer, mehr Leistung erbringen kann als versprochen wird.
Bei Interesse streben wir eine langfristige Zusammenarbeit an.
Im Anhang finden Sie Bildmaterial, was von einem anderen Produkt stammt mit Copyright!. Es geht be der Entwicklung um eine Dose von 250 ml Slim.
Es geht um die Entwicklung eines Design für ein neues Dosengetränk. Weitere Feinheiten und Einzelheiten per Telefon und oder Email.

```html
<!DOCTYPE html>
<html lang="en">
<head>
<meta charset="utf-8">
<title>Kesselbacher Tonic Water – Label</title>
<link rel="stylesheet" href="https://fonts.googleapis.com/css2?family=Cinzel:wght@400;600;700&display=swap">
<style>
  :root {
    --page-bg: #f2f0ec;
    --label-teal: #14a39b;
    --frame-white: #ffffff;
    --title-white: #ffffff;
    --title-shade: #6f7f7e;
    --brand-dark: #1b1b1b;
    --emblem-tone: #c9ecea;
  }
  * { margin: 0; padding: 0; box-sizing: border-box; }
  html, body {
    width: 1200px;
    height: 688px;
    overflow: hidden;
    background: var(--page-bg);
  }
  .canvas {
    position: relative;
    width: 1200px;
    height: 688px;
  }
  .label {
    position: absolute;
    left: 320px;
    top: 64px;
    width: 560px;
    height: 560px;
    background: var(--label-teal);
    font-family: "Cinzel", serif;
    text-align: center;
  }
  .label-frame {
    position: absolute;
    inset: 0;
  }
  .brand-name {
    position: absolute;
    top: 44px;
    left: 0;
    right: 0;
    font-weight: 700;
    font-size: 40px;
    letter-spacing: 1px;
    color: var(--brand-dark);
    line-height: 1;
  }
  .product-title {
    position: absolute;
    left: 0;
    right: 0;
    color: var(--title-white);
    font-weight: 400;
    line-height: 1;
    text-shadow: 2px 2px 0 var(--title-shade);
  }
  .product-title.tonic {
    top: 132px;
    font-size: 124px;
    letter-spacing: 2px;
  }
  .product-title.water {
    top: 278px;
    font-size: 88px;
    letter-spacing: 1px;
  }
  .emblem-area {
    position: absolute;
    left: 236px;
    top: 400px;
    width: 88px;
    height: 100px;
    background: var(--emblem-tone);
    opacity: 0.55;
  }
  .tagline {
    position: absolute;
    top: 520px;
    left: 0;
    right: 0;
    font-size: 19px;
    font-weight: 600;
    letter-spacing: 1.5px;
    color: var(--title-white);
    line-height: 1;
  }
</style>
</head>
<body>
  <main class="canvas">
    <section class="label" aria-label="Kesselbacher Tonic Water can label">
      <svg class="label-frame" width="560" height="560" viewBox="0 0 560 560" aria-hidden="true">
        <g stroke="var(--frame-white)" stroke-width="2.5" fill="none">
          <line x1="23" y1="23" x2="23" y2="532"/>
          <line x1="537" y1="23" x2="537" y2="532"/>
          <line x1="23" y1="23" x2="150" y2="23"/>
          <line x1="410" y1="23" x2="537" y2="23"/>
          <line x1="23" y1="532" x2="105" y2="532"/>
          <line x1="455" y1="532" x2="537" y2="532"/>
        </g>
      </svg>
      <div class="brand-name">KESSELBACHER</div>
      <h1 class="product-title tonic">TONIC</h1>
      <div class="product-title water">WATER</div>
      <div class="emblem-area" role="img" aria-label="Brand emblem"></div>
      <p class="tagline">A Superior Tonic Water</p>
    </section>
  </main>
</body>
</html>
```